Heron Loan Partners Business Card

We need a business card design for our mortgage servicing company. In addition to servicing the loans of homeowners, we help homeowners with purchasing their homes and any mortgage refinancing. We would like to see designs that use the colors in the logo attached below (gold-ish yellow and navy blue), and any other design you deem fit! The design should communicate a simpler life with smart mortgages provided by Heron.

```html
<!DOCTYPE html>
<html lang="en">
<head>
<meta charset="utf-8">
<title>Heron Loan Partners Business Card</title>
<link href="https://fonts.googleapis.com/css2?family=Arimo:wght@400;700&display=swap" rel="stylesheet">
<style>
  :root {
    --backdrop: #2a2a2c;
    --card-white: #f6f6f8;
    --gold: #d6b03f;
    --gold-deep: #cfa636;
    --navy: #1f1c5c;
    --text-light: #fdf7e6;
  }
  * { margin: 0; padding: 0; box-sizing: border-box; }
  html, body {
    width: 1200px; height: 750px; overflow: hidden;
    background: var(--backdrop);
    font-family: "Arimo", Arial, sans-serif;
  }
  .canvas { position: relative; width: 1200px; height: 750px; }
  .card {
    position: absolute;
    width: 560px; height: 320px;
    border-radius: 18px;
    overflow: hidden;
  }
  .card--front { left: 70px; top: 60px; background: var(--card-white); }
  .card--back {
    left: 570px; top: 370px;
    background: linear-gradient(135deg, var(--gold-deep), var(--gold));
  }
  .wordmark {
    position: absolute;
    display: flex; align-items: center; gap: 12px;
    font-weight: 700;
    white-space: nowrap;
  }
  .wordmark__dot { border-radius: 50%; flex: none; }
  .card--front .wordmark {
    left: 0; right: 0; top: 110px; justify-content: center;
    font-size: 50px; color: var(--navy);
  }
  .card--front .wordmark__dot { width: 22px; height: 22px; background: var(--gold); }
  .front__web {
    position: absolute; left: 0; right: 0; top: 238px;
    text-align: center; font-size: 14px; letter-spacing: 3px; color: var(--navy);
  }
  .card--back .wordmark {
    left: 40px; width: 230px; top: 146px; gap: 10px;
    font-size: 24px; color: #ffffff;
  }
  .card--back .wordmark__dot { width: 12px; height: 12px; background: var(--navy); }
  .back__divider {
    position: absolute; left: 292px; top: 36px;
    width: 1px; height: 190px; background: var(--text-light); opacity: .8;
  }
  .contact { position: absolute; left: 318px; top: 40px; color: var(--text-light); }
  .contact__name { font-size: 21px; font-weight: 700; color: var(--navy); }
  .contact__role { font-size: 13px; margin-top: 2px; }
  .contact__address { font-size: 13px; line-height: 1.45; margin-top: 14px; }
  .contact__lines { font-size: 13px; line-height: 1.5; margin-top: 12px; list-style: none; }
  .contact__lines b { color: var(--navy); display: inline-block; width: 28px; }
  .tagline {
    position: absolute; left: 0; right: 0; bottom: 34px;
    text-align: center; font-size: 15px; color: var(--navy);
    padding-left: 120px;
  }
</style>
</head>
<body>
<main class="canvas">
  <section class="card card--front" aria-label="Card front">
    <div class="wordmark"><span class="wordmark__dot"></span>Heron Mortgage</div>
    <p class="front__web">www.heron.com</p>
  </section>

  <section class="card card--back" aria-label="Card back">
    <div class="wordmark"><span class="wordmark__dot"></span>Heron Mortgage</div>
    <div class="back__divider"></div>
    <div class="contact">
      <p class="contact__name">Daniel Reyes</p>
      <p class="contact__role">President</p>
      <p class="contact__address">4120 Lakeview Terrace<br>Brookdale, NY 11590</p>
      <ul class="contact__lines">
        <li><b>P :</b>(555) 3146-7720</li>
        <li><b>E :</b>name@heron.com</li>
        <li><b>W :</b>www.heron.com</li>
      </ul>
    </div>
    <p class="tagline">Simpler life with smart mortgages</p>
  </section>
</main>
</body>
</html>
```